Accounting firm needing business card / letterhead designed
Marcus L. Trenholm, CPA
marcus@veltrowledger.com
www.veltrowledger.com
842 E Alder Ave Brackenfield, ND 43827
419-562-0974

```html
<!DOCTYPE html>
<html lang="en">
<head>
<meta charset="utf-8">
<title>Veltrow Ledger – Business Card</title>
<link href="https://fonts.googleapis.com/css2?family=Open+Sans:wght@400;600;700&display=swap" rel="stylesheet">
<style>
  :root {
    --navy: #29226a;
    --green: #8cc63f;
    --paper: #ffffff;
    --paper-shade: #e9e9ec;
    --ink: #2b2b2b;
    --backdrop: #2a2a2c;
  }
  * { margin: 0; padding: 0; box-sizing: border-box; }
  html, body {
    width: 1200px; height: 904px; overflow: hidden;
    background: var(--backdrop);
    font-family: "Open Sans", Arial, sans-serif;
  }
  .sheet {
    position: relative; width: 1200px; height: 904px;
    display: flex; flex-direction: column; align-items: center; justify-content: center; gap: 40px;
  }
  .card {
    position: relative; width: 640px; height: 366px; overflow: hidden;
    box-shadow: 0 10px 30px rgba(0,0,0,.45);
  }
  .card-back { background: var(--navy); display: flex; align-items: center; justify-content: center; }
  .wordmark {
    font-weight: 700; letter-spacing: 3px; text-transform: uppercase; line-height: 1; white-space: nowrap;
  }
  .card-back .wordmark { color: var(--paper); font-size: 40px; }

  .card-front { background: linear-gradient(120deg, var(--paper) 35%, var(--paper-shade) 100%); }
  .card-front .shapes { position: absolute; inset: 0; }
  .card-front .wordmark {
    position: absolute; left: 40px; top: 104px; color: var(--navy); font-size: 32px;
  }
  .holder-name {
    position: absolute; right: 26px; top: 11px;
    color: var(--green); font-weight: 700; font-size: 20px; white-space: nowrap;
  }
  .contact {
    position: absolute; left: 380px; top: 160px;
    color: var(--ink); font-size: 15px; line-height: 1.35; font-style: normal;
  }
  .contact .address { margin-bottom: 6px; }
  .contact-line { display: flex; align-items: center; gap: 10px; }
  .contact-line svg { width: 16px; height: 16px; flex: none; }
</style>
</head>
<body>
<main class="sheet">

  <section class="card card-back" aria-label="Card back">
    <span class="wordmark">Veltrow Ledger</span>
  </section>

  <section class="card card-front" aria-label="Card front">
    <svg class="shapes" viewBox="0 0 640 366" width="640" height="366" aria-hidden="true">
      <polygon points="318,0 640,0 640,48 282,48" fill="var(--navy)"/>
      <polygon points="0,344 640,302 640,366 0,366" fill="var(--navy)"/>
      <g fill="none" stroke="var(--paper)" stroke-width="5" stroke-linejoin="miter">
        <polyline points="232,326 222,336 232,346"/>
        <polyline points="246,325 236,335 246,345"/>
        <polyline points="260,324 250,334 260,344"/>
      </g>
    </svg>

    <span class="wordmark">Veltrow Ledger</span>
    <span class="holder-name">Marcus L. Trenholm, CPA</span>

    <address class="contact">
      <div class="address">842 E Alder Ave Brackenfield<br>ND 43827</div>
      <div class="contact-line">
        <svg viewBox="0 0 16 16"><circle cx="8" cy="8" r="8" fill="var(--navy)"/><path d="M5 4.5l1.6-.5 1 2-1 .8a5 5 0 0 0 2.6 2.6l.8-1 2 1-.5 1.6c-3.6.2-6.7-2.9-6.5-6.5z" fill="#fff"/></svg>
        <span>555-562-0974</span>
      </div>
      <div class="contact-line">
        <svg viewBox="0 0 16 16"><circle cx="8" cy="8" r="8" fill="var(--navy)"/><rect x="4" y="5" width="8" height="6" fill="#fff"/><path d="M4 5l4 3.5L12 5" fill="none" stroke="var(--navy)" stroke-width="1"/></svg>
        <span>marcus@veltrowledger.com</span>
      </div>
      <div class="contact-line">
        <svg viewBox="0 0 16 16"><circle cx="8" cy="8" r="8" fill="var(--navy)"/><circle cx="8" cy="8" r="4.5" fill="none" stroke="#fff"/><ellipse cx="8" cy="8" rx="2" ry="4.5" fill="none" stroke="#fff"/><line x1="3.5" y1="8" x2="12.5" y2="8" stroke="#fff"/></svg>
        <span>www.veltrowledger.com</span>
      </div>
    </address>
  </section>

</main>
</body>
</html>
```